Food broker, trader, wholesaler, liquidator looking for a 5 pages website

Looking for a 5 pages website design. We are food brokers, traders, wholesaler and closeout buyer working with manufacturers, distributors, importers sell to retailers, food service operators and industrial (ingredients). We help market their products. We are a resource for those who need a solution in the distribution/selling/placement of food on the shelves, kitchens and pantries. Whether we open new accounts with new products or sell short dated inventory, we know where to go and get results.

Target Market(s)

Food manufacturers, food distributors, food brokers

Coding

Coded - Design and coding required

Number of Pages Required

4 page

Font styles to use
Serif

Requirements
Must have
• Food-food production-warehouse-Food packaging-people meeting-trucks-supermarket shelves-

```html
<!DOCTYPE html>
<html lang="en">
<head>
<meta charset="utf-8">
<title>Harbor Provisions — Food Brokers &amp; Traders</title>
<link href="https://fonts.googleapis.com/css2?family=Montserrat:wght@400;500;600;700;800&family=Arimo:wght@400;700&display=swap" rel="stylesheet">
<style>
:root{
  --navy:#10145e;
  --navy-deep:#17186b;
  --ink:#1e1e1e;
  --body:#333;
  --muted:#8a8a8a;
  --steel:#1f2e45;
  --charcoal:#2d2d2d;
  --teal:#1d6e86;
  --green:#8dc63f;
  --blue:#1c5aa8;
  --white:#fff;
  --line:#dcdcdc;
}
*{margin:0;padding:0;box-sizing:border-box}
html,body{width:1200px;height:4041px;overflow:hidden}
body{position:relative;background:var(--white);font-family:"Arimo",Arial,sans-serif;color:var(--body)}
.abs{position:absolute}
.heading{font-family:"Montserrat",Arial,sans-serif;font-weight:700;color:var(--ink);letter-spacing:-0.5px}

/* header */
.header{top:0;left:0;width:1200px;height:128px;background:var(--white)}
.brand-dot{left:165px;top:8px;width:108px;height:86px;border-radius:50%;background:var(--navy)}
.brand-name{left:110px;top:98px;width:220px;text-align:center;font-family:"Montserrat",sans-serif;font-weight:700;font-size:14px;color:var(--navy)}
.nav a{position:absolute;top:60px;font-family:"Arimo",sans-serif;font-size:19px;color:#333;text-decoration:none}
.nav a.active{color:var(--navy)}
.call-icon{left:880px;top:47px;width:44px;height:44px;border-radius:50%;background:var(--navy)}
.call-label{left:933px;top:42px;font-size:19px;color:#222}
.call-number{left:933px;top:66px;font-size:23px;font-weight:700;color:#222}

/* hero */
.hero{top:128px;left:0;width:1200px;height:553px;background:linear-gradient(100deg,#c8b79a 0%,#d9cdb8 35%,#e4e2dc 55%,#b8c0c9 75%,#9b8a73 100%)}
.hero-title{left:110px;top:317px;font-size:40px;color:#1d1d1d}
.hero-text{left:111px;top:376px;width:470px;font-size:20px;line-height:36px;color:#222}
.btn-dark{left:110px;top:466px;width:174px;height:52px;background:#1f1f1f;color:#fff;font-family:"Montserrat",sans-serif;font-weight:600;font-size:20px;display:flex;align-items:center;justify-content:center}
.dot{top:645px;width:16px;height:16px;border-radius:50%;border:2px solid #333;background:rgba(255,255,255,.5)}

/* about */
.about-title{left:121px;top:785px;font-size:40px}
.about-lead{left:120px;top:856px;font-size:13.5px;color:#333}
.about-lead b{font-family:"Montserrat",sans-serif;font-size:21px;color:var(--navy);font-weight:600}
.about-text{left:121px;top:894px;width:530px;font-size:14.5px;line-height:32.7px;color:#333}
.btn-navy{left:118px;top:1109px;width:125px;height:44px;background:var(--navy);color:#fff;border-radius:3px;font-size:19px;display:flex;align-items:center;justify-content:center}
.photo-back{left:692px;top:846px;width:397px;height:297px;background:linear-gradient(135deg,#7c6a4a,#a9926b 40%,#4b5d80 100%)}
.photo-front{left:834px;top:985px;width:306px;height:196px;background:linear-gradient(135deg,#3d5fa8,#b88955 55%,#8e98a8);border:3px solid #fff}

/* what we do */
.services{top:1268px;left:0;width:1200px;height:589px;background:linear-gradient(180deg,#233349,#1c2c43)}
.services-title{left:0;width:1200px;top:1316px;text-align:center;font-size:40px;color:#fff}
.services-text{left:200px;width:800px;top:1395px;text-align:center;font-size:15.5px;line-height:34.5px;color:#fff}
.service{top:1550px;width:227px;height:220px;border:2px solid #e8e8e8;color:#fff;text-align:center}
.service svg{position:absolute;left:82px;top:14px}
.service h3{position:absolute;top:90px;left:0;width:100%;font-family:"Arimo",sans-serif;font-size:18.5px;font-weight:700;white-space:nowrap}
.service h3.compact{font-size:16px;top:92px}
.service p{position:absolute;top:120px;left:22px;right:22px;font-size:13.5px;line-height:25.5px}

/* process */
.process-title{left:0;width:1200px;top:1960px;text-align:center;font-size:40px}
.process-text{left:0;width:1200px;top:2032px;text-align:center;font-size:15px;line-height:34px;color:#222}
.step-label{top:2341px;width:180px;margin-left:-90px;text-align:center;font-size:17.5px;color:#333}

/* newsletter */
.newsletter{top:2493px;left:0;width:1200px;height:211px;background:linear-gradient(90deg,#2a2a2a,#3a3a3a 60%,#2c2c2c)}
.newsletter-title{left:108px;top:2542px;font-size:31px;color:#fff}
.newsletter-text{left:112px;top:2604px;font-size:15px;line-height:34px;color:#fff}
.field-pill{left:714px;top:2588px;width:375px;height:52px;border-radius:26px;background:#fff;border:2px solid #fff}
.field-pill span{position:absolute;left:28px;top:15px;font-size:14.5px;color:#444}
.pill-send{position:absolute;right:0;top:0;width:115px;height:48px;border-radius:24px;background:var(--navy);color:#fff;font-family:"Montserrat",sans-serif;font-weight:700;font-size:14.5px;display:flex;align-items:center;justify-content:center}

/* blog */
.blog-title{left:0;width:1200px;top:2800px;text-align:center;font-size:40px}
.post{border:1px solid var(--line);background:#fff}
.post-photo{position:absolute}
.post-date{position:absolute;font-family:"Montserrat",sans-serif;font-size:14px;font-weight:500;color:var(--navy)}
.post-title{position:absolute;font-family:"Montserrat",sans-serif;font-size:20.5px;line-height:27px;color:#222}
.post-text{position:absolute;font-size:12.5px;line-height:28px;color:#888}
.post-more{position:absolute;font-size:17px;color:var(--teal);letter-spacing:.3px}

/* footer */
.footer{top:3556px;left:0;width:1200px;height:485px;background:linear-gradient(160deg,#1b1c72,#141561)}
.footer-title{font-size:27px;color:#fff;font-weight:600}
.footer-item{left:154px;color:#fff;font-size:19px;line-height:31px}
.social{top:3879px;width:16px;height:16px;border-radius:50%;background:#fff}
.input{background:#fff;font-size:14.5px;color:#333;padding:15px 20px}
.btn-submit{left:756px;top:3928px;width:152px;height:49px;background:#fff;color:var(--navy);font-family:"Montserrat",sans-serif;font-weight:700;font-size:20px;display:flex;align-items:center;justify-content:center}
.copyright{left:108px;top:4005px;font-size:13px;color:#fff}
</style>
</head>
<body>

<!-- Header -->
<header class="abs header">
  <div class="abs brand-dot"></div>
  <div class="abs brand-name">HARBOR PROVISIONS</div>
  <nav class="nav">
    <a class="active" style="left:375px">Home</a>
    <a style="left:469px">About US</a>
    <a style="left:593px">What we do</a>
    <a style="left:739px">Contact Us</a>
  </nav>
  <div class="abs call-icon">
    <svg width="44" height="44" viewBox="0 0 44 44"><path d="M15 12c2 0 3 4 3 5s-2 2-2 3c1 3 4 6 7 7 1 0 2-2 3-2s5 1 5 3-2 4-4 4C18 32 12 26 12 16c0-2 1-4 3-4z" fill="#fff"/></svg>
  </div>
  <div class="abs call-label">Call Us</div>
  <div class="abs call-number">800-555-0142</div>
</header>

<!-- Hero -->
<section class="abs hero" role="img" aria-label="Food inspector in a white coat checking a tablet in a packaged-goods warehouse"></section>
<h1 class="abs heading hero-title">HARBOR PROVISIONS</h1>
<p class="abs hero-text">Lorem Ipsum is simply dummy text of the printing and typesetting industry. Lorem Ipsum.</p>
<div class="abs btn-dark">GET STARTED</div>
<div class="abs dot" style="left:568px"></div>
<div class="abs dot" style="left:592px"></div>
<div class="abs dot" style="left:616px"></div>

<!-- About -->
<h2 class="abs heading about-title">ABOUT US</h2>
<p class="abs about-lead"><b>We Expanded</b> into deli, dairy, groceries, frozen and beverages.</p>
<p class="abs about-text">Harbor Provisions works with food manufacturers, brand owners, distributors and wholesalers market their products.&nbsp; Retail, Food Service and Industrial ingredients. Founded in 2008, Harbor Provisions started with the distribution of gluten free products understanding the need to provide access to unique flavors and products forthe celiac consumers. From this,</p>
<div class="abs btn-navy">Read More</div>
<div class="abs photo-back" role="img" aria-label="Forklift in a warehouse aisle with tall shelving"></div>
<div class="abs photo-front" role="img" aria-label="Forklift carrying a pallet of cartons between blue racks"></div>

<!-- What we do -->
<section class="abs services" role="img" aria-label="Dim warehouse interior background"></section>
<h2 class="abs heading services-title">WHAT WE DO</h2>
<p class="abs services-text">We pride ourselves in working in aneasy, personal and accessible environment making our customers and vendors comfortable with us.We look forward to connecting with you and evaluating how we can assist you reaching your sales objectives.</p>

<div class="abs service" style="left:194px">
  <svg width="62" height="62" viewBox="0 0 62 62" fill="none" stroke="#fff" stroke-width="2"><rect x="22" y="6" width="20" height="18" rx="2"/><path d="M26 12h12M4 40l10-8h14l8 4-12 2M14 48h20l18-14-6-2-14 8"/></svg>
  <h3>Sales &amp; Marketing</h3>
  <p>connect food buyers and sellers through a dedicated approach</p>
</div>
<div class="abs service" style="left:488px">
  <svg width="62" height="62" viewBox="0 0 62 62" fill="none" stroke="#fff" stroke-width="2"><circle cx="14" cy="44" r="9"/><rect x="26" y="34" width="6" height="18"/><rect x="36" y="26" width="6" height="26"/><rect x="46" y="18" width="6" height="34"/><path d="M14 28l14-8 8 4 18-16M48 8h6v6"/></svg>
  <h3>Trading</h3>
  <p>we purchase goods anywhere and ship them Nationwide and Export.</p>
</div>
<div class="abs service" style="left:770px">
  <svg width="62" height="62" viewBox="0 0 62 62" fill="none" stroke="#fff" stroke-width="2"><rect x="6" y="6" width="50" height="50"/><path d="M6 22h50M6 38h50M18 10v8M30 10v8M42 10v8"/><rect x="14" y="42" width="12" height="10"/><rect x="34" y="26" width="14" height="10"/></svg>
  <h3 class="compact">Closeout/Excess Inventory</h3>
  <p>we buy closeouts and excess inventory for prisons, outlet stores and discounters.</p>
</div>

<!-- Process -->
<h2 class="abs heading process-title">OUR PROCESS</h2>
<p class="abs process-text">Neque porro quisquam est qui dolorem ipsum quia dolor sit amet, consectetur, adipisci velit...<br>There is no one who loves pain itself, who seeks after it and wants to have it simply.</p>

<svg class="abs" style="left:0;top:2150px" width="1200" height="190" viewBox="0 2150 1200 190">
  <line x1="158" y1="2235" x2="1052" y2="2235" stroke="#999" stroke-width="1"/>
  <g fill="none" stroke="#555" stroke-width="1.5">
    <path d="M158 2286v36M307 2286v36M460 2286v36M616 2286v36M770 2286v36M907 2286v36M1052 2286v36"/>
  </g>
  <g fill="#fff" stroke="#555" stroke-width="1.5">
    <circle cx="158" cy="2322" r="4"/><circle cx="307" cy="2322" r="4"/><circle cx="460" cy="2322" r="4"/><circle cx="616" cy="2322" r="4"/><circle cx="770" cy="2322" r="4"/><circle cx="907" cy="2322" r="4"/><circle cx="1052" cy="2322" r="4"/>
  </g>
  <g fill="#2f3136">
    <circle cx="158" cy="2235" r="51"/><circle cx="307" cy="2235" r="51"/><circle cx="460" cy="2235" r="51"/><circle cx="616" cy="2235" r="51"/><circle cx="770" cy="2235" r="51"/><circle cx="907" cy="2235" r="51"/><circle cx="1052" cy="2235" r="51"/>
  </g>
  <g fill="none" stroke="#fff" stroke-width="2">
    <path d="M134 2258v-26l24-16 24 16v26zM146 2258v-12h24v12M140 2236h36"/>
    <rect x="285" y="2210" width="44" height="48"/><path d="M285 2226h44M285 2242h44M296 2214v8M318 2214v8"/>
    <rect x="438" y="2210" width="44" height="48"/><path d="M438 2226h44M438 2242h44M449 2230v8M471 2230v8"/>
    <path d="M598 2212h24v46h-24zM622 2220h16v38h-16M604 2234h12v12h-12z"/>
    <rect x="748" y="2238" width="44" height="20"/><circle cx="760" cy="2222" r="6"/><circle cx="780" cy="2222" r="6"/><path d="M754 2248h32"/>
    <path d="M880 2218h32v28h-32zM912 2228h12l8 10v8h-20M888 2232l6 6 10-10"/><circle cx="892" cy="2250" r="4"/><circle cx="922" cy="2250" r="4"/>
    <path d="M1028 2212h48v10h-48zM1032 2222v36h40v-36M1040 2236h10v22h-10zM1056 2236h12v10h-12z"/>
  </g>
  <g fill="none" stroke="var(--green)" stroke-width="5" stroke-linecap="round">
    <path d="M200 2178q30-18 56 2"/><path d="M503 2178q30-18 56 2"/><path d="M805 2178q30-18 56 2"/>
  </g>
  <g fill="var(--green)">
    <path d="M250 2170l14 14-18 2z"/><path d="M553 2170l14 14-18 2z"/><path d="M855 2170l14 14-18 2z"/>
  </g>
  <g fill="none" stroke="var(--blue)" stroke-width="5" stroke-linecap="round">
    <path d="M350 2292q30 12 50-14"/><path d="M657 2292q30 12 50-14"/><path d="M950 2292q30 12 50-14"/>
  </g>
  <g fill="var(--blue)">
    <path d="M392 2268l16 2-10 16z"/><path d="M699 2268l16 2-10 16z"/><path d="M992 2268l16 2-10 16z"/>
  </g>
</svg>
<div class="abs step-label" style="left:158px">Food</div>
<div class="abs step-label" style="left:307px">Food production</div>
<div class="abs step-label" style="left:460px">Warehouse</div>
<div class="abs step-label" style="left:616px">Food packaging</div>
<div class="abs step-label" style="left:770px">People Meeting</div>
<div class="abs step-label" style="left:907px">Trucks</div>
<div class="abs step-label" style="left:1052px">supermarket shelves</div>

<!-- Newsletter -->
<section class="abs newsletter"></section>
<h2 class="abs heading newsletter-title">NEWSLETTER SUBSCRIPTION</h2>
<p class="abs newsletter-text">Lorem Ipsum is simply dummy text of the printing and typesetting industry.<br>Lorem Ipsum has been the industry's standard dummy.</p>
<div class="abs field-pill"><span>Enter Email Address</span><div class="pill-send">SEND</div></div>

<!-- Blog -->
<h2 class="abs heading blog-title">LATEST BLOG</h2>

<article class="abs post" style="left:111px;top:2913px;width:320px;height:543px">
  <div class="post-photo" role="img" aria-label="Worker walking down a tall warehouse aisle" style="left:0;top:0;width:318px;height:229px;background:linear-gradient(180deg,#2c4c8a,#6a6f7a 60%,#a78b62)"></div>
  <div class="post-date" style="left:33px;top:252px">Jan,2020</div>
  <div class="post-title" style="left:33px;top:286px;width:270px">Sed ut perspiciatis unde omnis iste natus</div>
  <div class="post-text" style="left:33px;top:354px;width:270px">Ut enim ad minima veniaquis nostreierci tationem ullam corpoboriosan isi utliquid ex ea commodi eprehenderitq ui in ea voluptmmodate velit .</div>
  <div class="post-more" style="left:34px;top:486px">READ MORE »</div>
</article>

<article class="abs post" style="left:447px;top:2913px;width:643px;height:264px">
  <div class="post-photo" role="img" aria-label="Cardboard shipping box on a conveyor" style="left:3px;top:3px;width:254px;height:258px;background:linear-gradient(150deg,#e6e1d8,#c9a06a 55%,#9f7a4a)"></div>
  <div class="post-date" style="left:291px;top:27px">Jan,2020</div>
  <div class="post-title" style="left:291px;top:60px;width:330px">Sed ut perspiciatis unde omnis iste natus error</div>
  <div class="post-text" style="left:291px;top:118px;width:330px">Ut enim ad minima veniam, quis nostreierci tationem ullam corporis suscipit laboriosan isi ut aliquid ex ea eprehenderitq utate velit .</div>
  <div class="post-more" style="left:295px;top:214px">READ MORE »</div>
</article>

<article class="abs post" style="left:447px;top:3192px;width:643px;height:264px">
  <div class="post-photo" role="img" aria-label="Two warehouse staff packing cardboard boxes" style="left:3px;top:3px;width:254px;height:258px;background:linear-gradient(150deg,#8c8a86,#6b6f7e 45%,#b08c63)"></div>
  <div class="post-date" style="left:291px;top:27px">Jan,2020</div>
  <div class="post-title" style="left:291px;top:60px;width:330px">Sed ut perspiciatis unde omnis iste natus error</div>
  <div class="post-text" style="left:291px;top:118px;width:330px">Ut enim ad minima veniam, quis nostreierci tationem ullam corporis suscipit laboriosan isi ut aliquid ex ea eprehenderitq utate velit .</div>
  <div class="post-more" style="left:295px;top:214px">READ MORE »</div>
</article>

<!-- Footer -->
<footer class="abs footer"></footer>
<h2 class="abs heading footer-title" style="left:108px;top:3606px">CONTACT US</h2>
<h2 class="abs heading footer-title" style="left:753px;top:3606px">GET IN TOUCH</h2>

<svg class="abs" style="left:111px;top:3676px" width="20" height="26" viewBox="0 0 20 26"><path d="M10 1a8 8 0 0 0-8 8c0 6 8 15 8 15s8-9 8-15a8 8 0 0 0-8-8z" fill="#fff"/><circle cx="10" cy="9" r="3" fill="#17186b"/></svg>
<div class="abs footer-item" style="top:3669px">Linden Street Studio<br>4120 Marlow Road, Dover</div>
<svg class="abs" style="left:108px;top:3760px" width="22" height="16" viewBox="0 0 22 16"><rect x="1" y="1" width="20" height="14" fill="none" stroke="#fff" stroke-width="2"/><path d="M1 1l10 8 10-8" fill="none" stroke="#fff" stroke-width="2"/></svg>
<div class="abs footer-item" style="top:3753px;font-size:18.5px">info@harborprovisions.com</div>
<svg class="abs" style="left:108px;top:3812px" width="22" height="22" viewBox="0 0 44 44"><path d="M10 4c4 0 6 8 6 10s-4 4-4 6c2 6 8 12 14 14 2 0 4-4 6-4s10 2 10 6-4 8-8 8C22 44 2 24 2 12 2 8 6 4 10 4z" fill="#fff"/></svg>
<div class="abs footer-item" style="top:3807px;font-size:22px">800-555-0142</div>
<div class="abs social" style="left:108px"></div>
<div class="abs social" style="left:157px"></div>
<div class="abs social" style="left:210px"></div>
<div class="abs social" style="left:262px"></div>
<div class="abs social" style="left:307px"></div>

<div class="abs input" style="left:571px;top:3671px;width:248px;height:47px">Name</div>
<div class="abs input" style="left:838px;top:3671px;width:248px;height:47px">Email</div>
<div class="abs input" style="left:571px;top:3734px;width:516px;height:47px">Phone Number</div>
<div class="abs input" style="left:571px;top:3796px;width:516px;height:107px">Message</div>
<div class="abs btn-submit">SUBMIT</div>
<div class="abs copyright">© 2020 All Rights Reserved | Privacy Policy | Terms and Conditions</div>

</body>
</html>
```